Yacht, Boats, Watersports company needs a redesign of business card

Hello Designers!
We are a Boat dealership company that sells fun in the water, we sell boats, Yachts, Kayaks and also yacht WaterSport toys. We are looking to redesign our business cards in to something a little bit more sophisticated. in a way that we can make better use of our company colors. I'm attaching a zipped file containing the company 3 sets of company logo which one is an horizontal another one is a vertical and also a chromed 3d logo. Also is included two set of business cards that we use and also some designs that i think it's interesting. We use PMS 2026c Orange and PMS 7687C Blue. I would like to see at least two different options with the orange as accent and also using blue as an accent color. It's really important for the business cards to have a font option and size that is legible to most people. Our current website is wwww.coralpennant.com. Please visit if you want to have a better feeling of the Boat dealership
You can send Single sided or double side options. We are now using single sided but we may be open for a double side option if we really like the design.
Target Market(s)
Marine, boat sales, yacht sales, water toys sales/
Contact Information for Business Card
Name: Dale Whitcombe
Address: 212 North Fenwick Lane,
Harbor Point, FL 33019
Phone: 954-731-8842
Fax: 954:731-8843
Cell: 954-382-1490
Email: dw@coralpennant.com
Website: coralpennant.com
Requirements
Must have
- the current information of the business card provided.
logo
use the PMS Colors
Nice to have
- a touch of elegance and sophistication but simple
Should not have
- should not have any typography that is hard to read, the card should be simple but yet sophisticated.

```html
<!DOCTYPE html>
<html lang="en">
<head>
<meta charset="utf-8">
<title>Coral Pennant Business Card</title>
<link rel="stylesheet" href="https://fonts.googleapis.com/css2?family=Poppins:wght@400;600&display=swap">
<style>
  :root {
    --backdrop: #b9babc;
    --card-blue: #1762b3;
    --accent-orange: #ef7d1a;
    --text-white: #ffffff;
  }
  html, body {
    margin: 0;
    padding: 0;
    width: 1200px;
    height: 800px;
    overflow: hidden;
    background: var(--backdrop);
    font-family: "Poppins", sans-serif;
  }
  .stage {
    width: 1200px;
    height: 800px;
    display: flex;
    align-items: center;
    justify-content: center;
    gap: 30px;
  }
  .card {
    position: relative;
    width: 560px;
    height: 320px;
    background: var(--card-blue);
    border-radius: 26px;
    border-bottom: 3px solid var(--accent-orange);
    box-sizing: border-box;
    overflow: hidden;
  }
  .card-front .brand-area {
    position: absolute;
    left: 34px;
    top: 40px;
    width: 236px;
    height: 236px;
    display: flex;
    align-items: center;
    justify-content: center;
  }
  .brand-ring {
    position: absolute;
    inset: 0;
    border: 14px solid var(--accent-orange);
    border-radius: 50%;
    box-sizing: border-box;
  }
  .brand-name {
    position: relative;
    color: var(--text-white);
    font-weight: 600;
    font-size: 26px;
    line-height: 1.15;
    text-align: center;
    letter-spacing: 0.02em;
  }
  .contact {
    position: absolute;
    right: 30px;
    top: 58px;
    text-align: right;
    color: var(--text-white);
    font-size: 13px;
    line-height: 1.5;
  }
  .contact-name {
    color: var(--accent-orange);
    font-weight: 600;
    font-size: 19px;
    letter-spacing: 0.03em;
    margin-bottom: 2px;
  }
  .contact-address { margin-bottom: 12px; }
  .contact-line {
    display: flex;
    justify-content: flex-end;
    align-items: center;
    gap: 8px;
  }
  .contact-line svg {
    width: 12px;
    height: 12px;
    fill: var(--accent-orange);
    flex: none;
  }
  .card-back {
    display: flex;
    flex-direction: column;
    align-items: center;
    justify-content: center;
    gap: 18px;
  }
  .back-ring {
    width: 70px;
    height: 70px;
    border: 8px solid var(--accent-orange);
    border-radius: 50%;
    box-sizing: border-box;
  }
  .back-name {
    color: var(--text-white);
    font-weight: 600;
    font-size: 34px;
    letter-spacing: 0.06em;
    text-transform: uppercase;
  }
</style>
</head>
<body>
<main class="stage">
  <section class="card card-front">
    <div class="brand-area">
      <div class="brand-ring"></div>
      <div class="brand-name">Coral<br>Pennant</div>
    </div>
    <div class="contact">
      <div class="contact-name">DALE WHITCOMBE</div>
      <div class="contact-address">212 North Fenwick Lane<br>Harbor Point, FL 33019</div>
      <div class="contact-line">954-731-8842
        <svg viewBox="0 0 24 24" aria-hidden="true"><path d="M6.6 10.8a15 15 0 0 0 6.6 6.6l2.2-2.2a1 1 0 0 1 1-.25 11.4 11.4 0 0 0 3.6.6 1 1 0 0 1 1 1V20a1 1 0 0 1-1 1A17 17 0 0 1 3 4a1 1 0 0 1 1-1h3.5a1 1 0 0 1 1 1c0 1.25.2 2.45.6 3.6a1 1 0 0 1-.25 1z"/></svg>
      </div>
      <div class="contact-line">954-382-1490
        <svg viewBox="0 0 24 24" aria-hidden="true"><path d="M7 1h10a2 2 0 0 1 2 2v18a2 2 0 0 1-2 2H7a2 2 0 0 1-2-2V3a2 2 0 0 1 2-2zm0 3v15h10V4z"/></svg>
      </div>
      <div class="contact-line">954-731-8843
        <svg viewBox="0 0 24 24" aria-hidden="true"><path d="M6 2h10l2 2v5h2a2 2 0 0 1 2 2v9a2 2 0 0 1-2 2H4a2 2 0 0 1-2-2v-9a2 2 0 0 1 2-2h2zm2 2v5h8V5.5L14.5 4zm2 9v2h8v-2z"/></svg>
      </div>
      <div class="contact-line">dw@coralpennant.com
        <svg viewBox="0 0 24 24" aria-hidden="true"><path d="M2 5h20v14H2zm2 2v.5l8 5 8-5V7zm0 2.8V17h16V9.8l-8 5z"/></svg>
      </div>
      <div class="contact-line">coralpennant.com
        <svg viewBox="0 0 24 24" aria-hidden="true"><path d="M12 2a10 10 0 1 0 0 20 10 10 0 0 0 0-20zm6.9 9h-3a15 15 0 0 0-1.3-6A8 8 0 0 1 18.9 11zM12 4.1c.9 1.3 1.7 3.6 1.9 6.9h-3.8c.2-3.3 1-5.6 1.9-6.9zM9.4 5a15 15 0 0 0-1.3 6h-3A8 8 0 0 1 9.4 5zM5.1 13h3a15 15 0 0 0 1.3 6A8 8 0 0 1 5.1 13zm6.9 6.9c-.9-1.3-1.7-3.6-1.9-6.9h3.8c-.2 3.3-1 5.6-1.9 6.9zm2.6-.9a15 15 0 0 0 1.3-6h3a8 8 0 0 1-4.3 6z"/></svg>
      </div>
    </div>
  </section>

  <section class="card card-back">
    <div class="back-ring"></div>
    <div class="back-name">Coral Pennant</div>
  </section>
</main>
</body>
</html>
```